Business Card Design

New business card design

Target Market(s)

Residential & Commercial Property Managers

Industry/Entity Type

Plumbing Services

Contact Information for Business Card

Name - Rowan Keddle, title - Director, Phone Number - 0431 286 517, email - rowan@tbk-plumbing.com.au, Company ABN - 73 215 904 386,

Font styles to use
Sans Serif

Colors
0054AA
0677BA
7BADD7
CADEEF
E8F1F8

```html
<!DOCTYPE html>
<html lang="en">
<head>
<meta charset="utf-8">
<title>TBK Plumbing Services – Business Card</title>
<link href="https://fonts.googleapis.com/css2?family=Montserrat:wght@400;500;700&display=swap" rel="stylesheet">
<style>
  :root {
    --stage: #262729;
    --card-white: #ffffff;
    --card-dark: #1c222b;
    --ink: #1d2129;
    --brand-blue: #29a8e0;
    --logo-light: #cadeef;
  }
  * { box-sizing: border-box; margin: 0; padding: 0; }
  html, body {
    width: 1200px; height: 1059px; overflow: hidden;
    background: var(--stage);
    font-family: "Montserrat", Arial, sans-serif;
    color: var(--ink);
  }
  .card {
    position: absolute; left: 256px; width: 690px; height: 392px;
    border-radius: 24px; overflow: hidden;
  }
  .card--front { top: 89px; background: var(--card-white); }
  .card--back { top: 546px; background: var(--card-dark); }

  .brand {
    position: absolute; display: flex; align-items: center; gap: 12px;
    font-weight: 700; white-space: nowrap;
  }
  .brand__dot { border-radius: 50%; background: var(--brand-blue); flex: none; }
  .card--front .brand { right: 40px; top: 66px; font-size: 30px; color: var(--ink); }
  .card--front .brand__dot { width: 22px; height: 22px; }
  .card--back .brand {
    left: 50%; top: 50%; transform: translate(-50%, -50%);
    font-size: 38px; color: var(--logo-light);
  }
  .card--back .brand__dot { width: 28px; height: 28px; }

  .person { position: absolute; left: 33px; top: 204px; }
  .person__name { font-size: 24px; font-weight: 700; line-height: 1.1; }
  .person__title { font-size: 14px; font-weight: 500; margin-top: 3px; }
  .divider {
    position: absolute; left: 33px; right: 41px; top: 254px;
    height: 2px; background: var(--ink);
  }

  .contacts { position: absolute; left: 37px; top: 282px; list-style: none; }
  .contacts li {
    display: flex; align-items: center; gap: 10px;
    font-size: 14.5px; font-weight: 500; height: 27px;
  }
  .contacts svg { width: 16px; height: 16px; fill: var(--brand-blue); flex: none; }

  .address {
    position: absolute; right: 50px; top: 296px;
    font-size: 15px; font-weight: 500; line-height: 1.2; text-align: left;
  }

  .footer-bands { position: absolute; left: 0; bottom: 0; width: 690px; height: 38px; }
  .abn {
    position: absolute; right: 32px; bottom: 10px;
    font-size: 14px; font-weight: 500; color: var(--ink);
  }
  .abn strong { font-weight: 700; }
</style>
</head>
<body>

<section class="card card--front" aria-label="Business card front">
  <div class="brand"><span class="brand__dot"></span>TBK Plumbing Services</div>

  <div class="person">
    <div class="person__name">Rowan Keddle</div>
    <div class="person__title">Director</div>
  </div>
  <div class="divider"></div>

  <ul class="contacts">
    <li>
      <svg viewBox="0 0 24 24" aria-hidden="true"><path d="M6.6 10.8a15.1 15.1 0 0 0 6.6 6.6l2.2-2.2c.3-.3.7-.4 1-.2 1.1.4 2.3.6 3.6.6.6 0 1 .4 1 1V20c0 .6-.4 1-1 1C10.6 21 3 13.4 3 4c0-.6.4-1 1-1h3.5c.6 0 1 .4 1 1 0 1.3.2 2.5.6 3.6.1.3 0 .7-.2 1z"/></svg>
      0431 286 517
    </li>
    <li>
      <svg viewBox="0 0 24 24" aria-hidden="true"><path d="M2 5h20v2l-10 6L2 7zM2 9l10 6 10-6v10H2z"/></svg>
      rowan@tbk-plumbing.com.au
    </li>
    <li>
      <svg viewBox="0 0 24 24" aria-hidden="true"><path d="M12 2a10 10 0 1 0 0 20 10 10 0 0 0 0-20zm-1 17.9A8 8 0 0 1 4.2 10.8L9 15.5v1c0 1.1.9 2 2 2zm6.9-2.5A2 2 0 0 0 16 16h-1v-3a1 1 0 0 0-1-1H8v-2h2a1 1 0 0 0 1-1V7h2a2 2 0 0 0 2-2v-.4a8 8 0 0 1 2.9 12.8z"/></svg>
      www.tbk-plumbing.com.au
    </li>
  </ul>

  <div class="address">27 Banksia Crest Way<br>Kiama, NSW 2533</div>

  <svg class="footer-bands" viewBox="0 0 690 38" preserveAspectRatio="none" aria-hidden="true">
    <rect x="0" y="19" width="690" height="19" fill="var(--card-dark)"/>
    <polygon points="423,38 442,19 453,19 434,38" fill="var(--card-white)"/>
    <polygon points="434,38 466,0 690,0 690,38" fill="var(--brand-blue)"/>
  </svg>
  <div class="abn"><strong>ABN</strong> - 73 215 904 386</div>
</section>

<section class="card card--back" aria-label="Business card back">
  <div class="brand"><span class="brand__dot"></span>TBK Plumbing Services</div>
</section>

</body>
</html>
```